Start-up braucht modernes/hochwertiges Getränkeetikett
Zielgruppe
Wir sind ein modernes, nachhaltiges Start-up, welches eine neue Getränkekategorie auf den Markt bringt. Ein sogenanntes Elektrolyt-Getränk mit dem Namen FLUXO4. Es ist abgefüllt in eine 500 ml Flasche und enthält Magnesium, Kalzium, Kalium, und Natrium. Diese Stoffe (Elektrolyte) dienen der körperlichen Hydrierung. Zu Dehydrierung kann es durch Hitze, Alkohol, Sport oder Krankheit kommen. Krankheit liegt bei uns allerdings nicht im Fokus. In unserer Zielgruppe befinden sich hauptsächlich Personen im Alter von 18 - 29 Jahren.
Die Geschmacksrichtung ist Zitrone-Limette.
Aufgabenstellung
Das Etikett soll:
- MODERN, SCHLICHT und HOCHWERTIG sein, so dass es im Supermarkt hervorsticht
- erkenntlich machen, dass die Stoffe Magnesium, Natrium, Kalzium und Kalium enthalten sind
- sich farblich deutlich von der Farbe des Inhalts (weiß) abheben. (Vorzugsweise mit einem hellen Blau, türkis)
- für unsere junge Zielgruppe ansprechend sein
- ebenfalls auf die Geschmacksrichtung (Zitrone-Limette) hinweisen, und zwar so, dass wenn man eine weitere Geschmacksrichtung auf den Markt bringen möchte, diese leicht angepasst werden kann.
- nicht nach einem Energydrink oder einem typischen Sportgetränk aussehen
- unter dem Namen den Slogan 'Elektrolyt-Getränk' stehen haben
-Das Etikett ist nicht dursichtig sondern besteht aus Papier
Der Name sowie das Logo können selbstverständlich farblich verändert werden. Bei dem Logo können auch größere Änderungen vollzogen werden.
Bitte beachten Sie die unten zu stehenden Regler um sich einen guten Überblick über unsere Vorstellungen zu verschaffen. Die Platzierung des EAN-Code ist für ihr Design irrelevat .
Bei Unklarheiten gerne nachfragen!

```html
<!DOCTYPE html>
<html lang="de">
<head>
<meta charset="utf-8">
<title>FLUXO4 – Elektrolyt-Getränk Etikett</title>
<link href="https://fonts.googleapis.com/css2?family=Quicksand:wght@300;700&display=swap" rel="stylesheet">
<style>
  :root {
    --page-bg: #e4e5e8;
    --label-light: #a8bccb;
    --label-mid: #2a5274;
    --label-deep: #0b1a3c;
    --label-edge: #8a93a6;
    --ink-white: #f4f6f8;
    --lemon-light: #cbcc8e;
    --lemon-deep: #858512;
    --lemon-ink: #6c7a12;
    --lime-light: #95b889;
    --lime-deep: #1f6b1c;
    --lime-ink: #8ea82a;
  }
  * { margin: 0; padding: 0; box-sizing: border-box; }
  html, body {
    width: 667px;
    height: 1200px;
    overflow: hidden;
  }
  body {
    background: var(--page-bg);
    font-family: "Quicksand", sans-serif;
    position: relative;
  }
  .label {
    position: absolute;
    left: 33px;
    top: 135px;
    width: 600px;
    height: 930px;
    overflow: hidden;
    background:
      radial-gradient(ellipse 60% 55% at 68% 78%, rgba(5,14,40,0.95) 0%, rgba(5,14,40,0) 70%),
      linear-gradient(100deg, var(--label-light) 0%, #8ea5b9 22%, var(--label-mid) 48%, var(--label-deep) 62%, #3d5a78 80%, var(--label-edge) 100%);
  }
  .label-top {
    position: absolute;
    inset: 0 0 auto 0;
    height: 840px;
  }
  .emblem-ring {
    position: absolute;
    left: 151px;
    top: 98px;
    width: 270px;
    height: 270px;
    border: 3px solid var(--ink-white);
    border-radius: 50%;
  }
  .brand-name {
    position: absolute;
    left: 0;
    right: 0;
    top: 440px;
    text-align: center;
    font-weight: 700;
    font-size: 80px;
    line-height: 1;
    letter-spacing: 1px;
    color: var(--ink-white);
  }
  .tagline {
    position: absolute;
    left: 0;
    right: 0;
    top: 558px;
    text-align: center;
    font-weight: 300;
    font-size: 39px;
    letter-spacing: 0.5px;
    color: var(--ink-white);
  }
  .minerals {
    position: absolute;
    left: 0;
    right: 0;
    top: 655px;
    list-style: none;
    text-align: center;
    font-weight: 700;
    font-size: 21px;
    line-height: 42.5px;
    color: var(--ink-white);
  }
  .flavour-band {
    position: absolute;
    left: 0;
    right: 0;
    text-align: center;
    font-weight: 700;
    font-size: 21px;
    letter-spacing: 0.5px;
  }
  .flavour-band--lemon {
    top: 840px;
    height: 49px;
    line-height: 49px;
    background: linear-gradient(90deg, var(--lemon-light) 0%, #b9ba6a 35%, var(--lemon-deep) 60%, #a5a650 85%, #b3b380 100%);
    color: var(--lemon-ink);
  }
  .flavour-band--lime {
    top: 889px;
    height: 41px;
    line-height: 41px;
    background: linear-gradient(90deg, var(--lime-light) 0%, #6fa063 35%, var(--lime-deep) 60%, #4d8a48 85%, #78a07c 100%);
    color: var(--lime-ink);
  }
</style>
</head>
<body>
  <main class="label" aria-label="Getränkeetikett FLUXO4">
    <section class="label-top">
      <div class="emblem-ring" aria-hidden="true"></div>
      <h1 class="brand-name">FLUXO4</h1>
      <p class="tagline">ELEKTROLYT-GETRÄNK</p>
      <ul class="minerals">
        <li>Magnesium</li>
        <li>Natrium</li>
        <li>Kalcium</li>
        <li>Kalium</li>
      </ul>
    </section>
    <div class="flavour-band flavour-band--lemon">ZITRONE</div>
    <div class="flavour-band flavour-band--lime">LIMETTE</div>
  </main>
</body>
</html>
```